Maple Sprout Menu (Vegetarian Restaurant Concept)

Maple Sprout is a new concept fast casual restaurant
renders are attached so you can see the style of restaurant
Maple Sproute is a vibrant and modern Vegetarian fast casual restaurant concept that mixes fresh food, energy, great décor, and a comfortable, welcoming atmosphere to provide a memorable and all Vegetarian dining experience.
Our Mission is to be top of mind when consumers think Vegetarian food!
Updates
Need extra days to review
Target Market(s)
the menu is vegetarian and appeals to a broad demographic in USA
Font styles to use
Colors
Designer to choose colors to be used in the design.
Requirements
Must have
- well colored and well laid out menu - should not be cartoonish
Nice to have
- For Phots please use the shots in this file:
- https://www.filecrate-share.net/sh/qtrv8knw2lpa5zc/BBBxR_pLmNoQwEE4J_TKX_Va?dl=0
- note these are untouched and you are free to change as needed
Should not have
- Should not be cartoonish - nor kives, forks etc in the design

```html
<!DOCTYPE html>
<html lang="en">
<head>
<meta charset="utf-8">
<title>Maple Sprout Menu</title>
<link rel="stylesheet" href="https://fonts.googleapis.com/css2?family=Didact+Gothic&family=Arimo:wght@700&display=swap">
<style>
  :root {
    --leaf: #8cc43f;
    --ink: #24282b;
    --paper: #ffffff;
    --board: #4b4b4f;
    --board-deep: #3c3c40;
    --panel: rgba(70, 70, 76, 0.55);
    --text: #f4f4f4;
    --rule: #d8d8d8;
  }
  * { margin: 0; padding: 0; box-sizing: border-box; }
  html, body { width: 846px; height: 1200px; overflow: hidden; }
  body { font-family: "Didact Gothic", "Century Gothic", sans-serif; color: var(--text); }

  .menu-sheet { position: relative; width: 846px; height: 1200px; background: var(--board); overflow: hidden; }

  .brand-block { position: absolute; left: 0; top: 0; width: 175px; height: 230px; background: var(--paper);
    display: flex; flex-direction: column; align-items: center; justify-content: center; gap: 14px; }
  .brand-dot { width: 46px; height: 46px; border-radius: 50%; background: var(--leaf); }
  .brand-name { font-size: 21px; color: var(--ink); text-align: center; line-height: 1.15; }

  .hero-photo { position: absolute; left: 175px; top: 0; width: 671px; height: 230px;
    background:
      radial-gradient(circle at 18% 48%, #e6d2a8 0 23%, transparent 24%),
      radial-gradient(circle at 50% 60%, #7da450 0 25%, #efe9dc 26% 30%, transparent 31%),
      radial-gradient(circle at 85% 46%, #8a2238 0 20%, #efe9dc 21% 26%, transparent 27%),
      linear-gradient(90deg, #b59a7c, #a88c6d 50%, #bca385); }

  .title-band { position: absolute; left: 0; top: 230px; width: 846px; height: 113px; background: var(--leaf);
    display: flex; align-items: center; justify-content: center; }
  .title-band h1 { font-family: "Arimo", Arial, sans-serif; font-weight: 700; font-size: 74px; color: var(--paper); letter-spacing: 1px; padding-top: 6px; }

  .board-surface { position: absolute; left: 0; top: 343px; width: 846px; height: 857px;
    background: linear-gradient(180deg, var(--board) 0%, var(--board-deep) 100%); }

  .produce-photo { position: absolute; left: 0; top: 935px; width: 846px; height: 265px;
    background:
      radial-gradient(ellipse 26% 55% at 12% 75%, #d8401f 0 60%, transparent 61%),
      radial-gradient(ellipse 14% 45% at 34% 90%, #c8212a 0 60%, transparent 61%),
      radial-gradient(ellipse 10% 26% at 52% 75%, #d9ccb8 0 60%, transparent 61%),
      radial-gradient(ellipse 12% 48% at 62% 95%, #7aa84a 0 60%, transparent 61%),
      radial-gradient(ellipse 10% 30% at 92% 100%, #a54678 0 60%, transparent 61%),
      linear-gradient(180deg, transparent 0%, rgba(60,60,64,0) 100%); }

  .panel { position: absolute; background: var(--panel); border-radius: 8px; }
  .panel-salads { left: 18px; top: 376px; width: 398px; height: 272px; }
  .panel-toasts { left: 18px; top: 672px; width: 398px; height: 156px; }
  .panel-soup { left: 18px; top: 852px; width: 398px; height: 96px; }
  .panel-right { left: 432px; top: 376px; width: 400px; height: 572px; }

  .section-title { position: absolute; font-size: 21px; letter-spacing: 0.5px; line-height: 1; white-space: nowrap; }
  .section-rule { position: absolute; height: 1px; background: var(--rule); }

  .dish { position: absolute; text-align: center; white-space: nowrap; }
  .col-left { left: 18px; width: 398px; }
  .col-right { left: 432px; width: 400px; }
  .dish-name { font-size: 14px; letter-spacing: 1.3px; line-height: 17px; }
  .dish-desc { font-size: 11px; letter-spacing: 0.5px; line-height: 14px; }
  .divider { position: absolute; height: 1px; width: 62px; background: var(--rule); }
</style>
</head>
<body>
<main class="menu-sheet">
  <div class="brand-block">
    <div class="brand-dot"></div>
    <div class="brand-name">Maple Sprout</div>
  </div>
  <div class="hero-photo" role="img" aria-label="Photo of three takeaway bowls on wood: quesadilla wedges with dip, brussels sprout caesar salad, and beet salad"></div>
  <header class="title-band"><h1>MENU</h1></header>
  <div class="board-surface"></div>
  <div class="produce-photo" role="img" aria-label="Photo of fresh vegetables: tomatoes, red pepper, mushrooms, carrots and greens"></div>

  <section class="panel panel-salads"></section>
  <section class="panel panel-toasts"></section>
  <section class="panel panel-soup"></section>
  <section class="panel panel-right"></section>

  <!-- Salads -->
  <h2 class="section-title" style="left:60px;top:388px">SALADS</h2>
  <div class="section-rule" style="left:55px;top:413px;width:325px"></div>
  <div class="dish col-left" style="top:433px"><p class="dish-name">BRUSSEL SPROUT CAESAR</p><p class="dish-desc">little gem romaine, toasted torn bread, parmiggiano reggiano</p></div>
  <div class="dish col-left" style="top:474px"><p class="dish-name">HEIRLOOM BEET SALAD</p><p class="dish-desc">shaved chioggia beet, roasted golden beet, red quinoa</p><p class="dish-desc">little gem, arugula, lemon vinaigrette</p></div>
  <div class="divider" style="left:186px;top:521px"></div>
  <div class="dish col-left" style="top:533px"><p class="dish-name">ZESTY BLACK BEAN &amp; CORN SALAD IN LETTUCE CUPS</p><p class="dish-desc">black beans, avocado and roasted corn topped with feta crumbles</p><p class="dish-desc">in butter lettuce</p></div>
  <div class="divider" style="left:186px;top:583px"></div>
  <div class="dish col-left" style="top:591px"><p class="dish-name">GREEN, RED &amp; WHITE</p><p class="dish-desc">spring leaves, cherry tomatoes, avocado</p><p class="dish-desc">roasted almond and goat cheese</p></div>

  <!-- Toasts -->
  <h2 class="section-title" style="left:61px;top:688px">TOASTS</h2>
  <div class="section-rule" style="left:55px;top:712px;width:325px"></div>
  <div class="dish col-left" style="top:732px"><p class="dish-name">EVERYTHING AVOCADO TOAST</p><p class="dish-desc">avocado on whole grain toast with our signature spice blend</p></div>
  <div class="divider" style="left:186px;top:767px"></div>
  <div class="dish col-left" style="top:773px"><p class="dish-name">TOMATO &amp; BEET BRUSCHETTA</p></div>
  <div class="divider" style="left:186px;top:795px"></div>
  <div class="dish col-left" style="top:799px"><p class="dish-name">VEGETABLE MELT ON GARLIC TOAST</p></div>

  <!-- Soup -->
  <h2 class="section-title" style="left:58px;top:872px">SOUP</h2>
  <div class="section-rule" style="left:55px;top:897px;width:325px"></div>
  <div class="dish col-left" style="top:916px"><p class="dish-name">BLACK BEAN CHOWDER</p></div>

  <!-- Burgers / Wraps / Sandwiches -->
  <h2 class="section-title" style="left:434px;top:388px;word-spacing:4px">BURGERS / WRAPS / SANDWICHES</h2>
  <div class="section-rule" style="left:470px;top:413px;width:325px"></div>
  <div class="dish col-right" style="top:433px"><p class="dish-name">SWEET POTATO, BLACK BEAN VEGGIE BURGER</p><p class="dish-desc">with cabbage – pepita slaw</p></div>
  <div class="dish col-right" style="top:474px"><p class="dish-name">ROASTED VEGGIE, ARUGULA AND HUMMUS WRAP</p></div>
  <div class="divider" style="left:601px;top:500px"></div>
  <div class="dish col-right" style="top:506px"><p class="dish-name">GARDEN BURGER</p></div>
  <div class="divider" style="left:601px;top:530px"></div>
  <div class="dish col-right" style="top:536px"><p class="dish-name">BEANS &amp; GREENS QUESADDILLA</p><p class="dish-desc">greens, Mexican cheese, beans, avocado, salsa</p></div>
  <div class="divider" style="left:601px;top:575px"></div>
  <div class="dish col-right" style="top:581px"><p class="dish-name">VEGGIE BURRITO</p><p class="dish-desc">greens, Mexican cheese, beans, brown rice, roasted chilli corn</p><p class="dish-desc">avocado, ancho chilli salsa, wheat tortilla</p></div>

  <!-- Bowls -->
  <h2 class="section-title" style="left:467px;top:643px">BOWLS</h2>
  <div class="section-rule" style="left:470px;top:668px;width:325px"></div>
  <div class="dish col-right" style="top:688px"><p class="dish-name">ROASTED VEGETABLE &amp; SPINACH</p></div>
  <div class="divider" style="left:571px;top:711px;width:122px"></div>
  <div class="dish col-right" style="top:717px"><p class="dish-name">SUGAR SNAP PEA &amp; CARROT SOBA NOODLES</p></div>
  <div class="divider" style="left:571px;top:744px;width:122px"></div>
  <div class="dish col-right" style="top:750px"><p class="dish-name">WHOLE GRAIN AND VEGETABLE BUDDHA</p></div>
  <div class="divider" style="left:571px;top:774px;width:122px"></div>
  <div class="dish col-right" style="top:780px"><p class="dish-name">ORANGE &amp; PISTACIO QUINOA</p></div>

  <!-- Desserts -->
  <h2 class="section-title" style="left:467px;top:812px">DESSERTS</h2>
  <div class="section-rule" style="left:470px;top:838px;width:325px"></div>
  <div class="dish col-right" style="top:857px"><p class="dish-name">STRAWBERRY BALSAMIC ICE CREAM SUNDAE</p></div>
  <div class="dish col-right" style="top:887px"><p class="dish-name">EXOTIC FRUIT BOWL</p></div>
  <div class="divider" style="left:571px;top:912px;width:122px"></div>
  <div class="dish col-right" style="top:919px"><p class="dish-name">WHITE AND DARK OATMEAL COOKIE</p></div>
</main>
</body>
</html>
```